Landingpage Design X-Mas Invitation

Every year we invite customers to a special X-Mas Apéro. Since we are an IT-Company we handle the registration process by a landingpage. For this we need a design for the event 2016. The content will be the same as 2015 (you will finde the design attached from last year. There will be an additional job for creating the E-Mail.

Target Market(s)

Customers of IT Company, medium Companys in Central Switzerland

Industry/Entity Type

It Company

Number of Pages Required

1 page

Requirements
Must have
• Christmas Style

```html
<!DOCTYPE html>
<html lang="de">
<head>
<meta charset="utf-8">
<title>Lumivar Weihnachtsapéro 2016</title>
<link rel="stylesheet" href="https://fonts.googleapis.com/css2?family=Roboto:wght@400;500&family=Roboto+Condensed:ital,wght@0,400;1,400&display=swap">
<style>
  :root {
    --brand-red: #c0392b;
    --band-top: #b50f1f;
    --band-mid: #95071a;
    --band-bottom: #5c000c;
    --white: #ffffff;
    --badge-border: #e3e3e3;
    --badge-fill: #cfcfcf;
    --footer-bg: #1e1e1e;
    --footer-text: #e8e8e8;
  }
  * { box-sizing: border-box; margin: 0; padding: 0; }
  html, body { width: 1200px; height: 1161px; overflow: hidden; background: var(--white); }
  body { position: relative; font-family: "Roboto", Arial, sans-serif; color: var(--white); }

  .site-header {
    position: absolute; left: 0; top: 0; width: 1200px; height: 113px;
    border-top: 3px solid var(--brand-red); background: var(--white);
    display: flex; align-items: center; justify-content: center;
  }
  .brand-name {
    font-family: "Roboto", Arial, sans-serif; font-weight: 500;
    font-size: 40px; color: var(--brand-red); letter-spacing: 0.5px;
  }

  .invitation {
    position: absolute; left: 0; top: 113px; width: 1200px; height: 788px;
    background: linear-gradient(180deg, var(--band-top) 0%, var(--band-mid) 55%, var(--band-bottom) 100%);
    overflow: hidden;
  }
  .tree-artwork {
    position: absolute; left: 128px; top: 155px; width: 462px; height: 510px;
    background: radial-gradient(ellipse at 50% 55%, rgba(255,255,255,0.28) 0%, rgba(255,230,150,0.14) 40%, rgba(255,255,255,0) 72%);
  }
  .event-name {
    position: absolute; left: 115px; top: 213px;
    font-size: 19px; line-height: 28px;
  }
  .event-date {
    position: absolute; left: 378px; top: 256px;
    font-size: 19px; line-height: 25px;
    transform: rotate(-35deg); transform-origin: left bottom;
    white-space: nowrap;
  }

  .registration { position: absolute; left: 616px; top: 0; width: 494px; }
  .intro { position: absolute; top: 68px; width: 494px; font-size: 16px; line-height: 22px; }
  .intro p + p { margin-top: 22px; }
  .section-title {
    position: absolute; font-family: "Roboto Condensed", Arial, sans-serif;
    font-style: italic; font-size: 23px; font-weight: 400;
  }
  .field {
    position: absolute; height: 39px; border: 2px solid var(--white); border-radius: 20px;
    padding-left: 26px; display: flex; align-items: center;
    font-size: 13px; color: rgba(255,255,255,0.85);
  }
  .field--wide { width: 493px; left: 0; }
  .field--half { width: 237px; }
  .field--left { left: 0; }
  .field--right { left: 255px; }

  .action-link {
    position: absolute; left: 2px; font-size: 21px; font-weight: 500;
    color: var(--white); text-decoration: underline; text-underline-offset: 3px;
  }

  .partners {
    position: absolute; left: 0; top: 901px; width: 1200px; height: 178px; background: var(--white);
  }
  .partner-badge {
    position: absolute; top: 42px; width: 153px; height: 93px;
    border: 1px solid var(--badge-border);
    display: flex; align-items: center; justify-content: center;
  }
  .partner-badge span { width: 48px; height: 48px; border-radius: 50%; background: var(--badge-fill); }

  .site-footer {
    position: absolute; left: 0; top: 1079px; width: 1200px; height: 82px;
    background: var(--footer-bg); color: var(--footer-text);
    font-size: 14px; text-align: center; line-height: 82px;
  }
</style>
</head>
<body>
  <header class="site-header">
    <span class="brand-name">Lumivar</span>
  </header>

  <section class="invitation">
    <div class="tree-artwork" role="img" aria-label="Illustration eines Weihnachtsbaums aus bunten Sternen und weissen Funken"></div>
    <p class="event-name">Lumivar<br>Weihnachts<br>apéro</p>
    <p class="event-date">17. Dezember 2016<br>&nbsp;&nbsp;&nbsp;17 – 20 Uhr</p>

    <div class="registration">
      <div class="intro">
        <p>Ob Sie den ganzen Abend bleiben oder nur kurz nach dem Weihnachts-Shopping vorbeischauen, ist ganzIhnen uberlassen.</p>
        <p>Wir freuen uns sehr, wenn Sie uns die Gelegenheit geben, Ihnen mit dieser Einladung for die</p>
        <p>erfolgreiche Zusammenarbeit herzlichst zu danken.</p>
      </div>

      <h2 class="section-title" style="top:270px;">Ihre Anmeldung</h2>
      <div class="field field--wide" style="top:317px;">Ihre E-mail-Adresse</div>
      <div class="field field--half field--left" style="top:369px;">Vorname</div>
      <div class="field field--half field--right" style="top:369px;">Nachname</div>

      <h2 class="section-title" style="top:466px;">Ihre Begleitperson</h2>
      <div class="field field--wide" style="top:515px;">Firma (Optional)</div>
      <div class="field field--half field--left" style="top:566px;">Vorname</div>
      <div class="field field--half field--right" style="top:566px;">Nachname</div>

      <a class="action-link" href="#" style="top:651px;">Weitere Begleitperson</a>
      <a class="action-link" href="#" style="top:679px;">Absenden</a>
    </div>
  </section>

  <section class="partners" aria-label="Partner">
    <div class="partner-badge" style="left:73px;"><span></span></div>
    <div class="partner-badge" style="left:253px;"><span></span></div>
    <div class="partner-badge" style="left:433px;"><span></span></div>
    <div class="partner-badge" style="left:613px;"><span></span></div>
    <div class="partner-badge" style="left:793px;"><span></span></div>
    <div class="partner-badge" style="left:973px;"><span></span></div>
  </section>

  <footer class="site-footer">Copyright ©, Lumivar.&nbsp; All Rights Reserved.</footer>
</body>
</html>
```